Novexa company website, a website for employment for people with autism

The website will make a match between people and jobs, mainly in the graphical sector, but also other sectors.
The name of the company is novexa and automates jobs with people that are on the autism spectrum.
The whole matchmaking and feedback process and so doesn't have to be in this prototype, we just want the general information pages and to convey a great look and brand identity that we will keep in the other pages to be developed. The website must be made with Wordpress, since the backend will be developed in Wordpress too.
It is a social project that wants to create possibilites for people with ASS to work from home for an employer or to do a variety of tasks for different customers.
The people we hire are generally not on the regular job market or have difficulty finding a job and "selling themselves"

Target Market(s)

matchmaking between talent (with ASS) and employers / jobs

Number of Pages Required

5+ page

Font styles to use
Sans Serif

Colors
ec1f27
e34298
a64599
6b449b
0355a3
0792cd

Requirements
Must have
• A stunning landing pages
• Integrate our logo and must match with what will do. We want a clean, modern, minimalistic, sleek website that radiates creativity and good looks.
• We have one page describing what we can do for customers, one page for people with ASS that would like to be candidates (our approach, learning program, ...), two pages that are addressed to partners who want to cooperate: the one's that can assist with autism related assistance and the one's that can help with the job coaching.
Nice to have
• In our logo are many colors as we embrace diversity and want to show that. Out main branding colors are red (for action) and blue for stability and will all gradients that go with it. Mainly white or black (or anthracite) for other parts
Should not have
• We want a modern and minimalistic design, no fluffy designs with lots of ornaments.

```html
<!DOCTYPE html>
<html lang="en">
<head>
<meta charset="utf-8">
<title>Novexa — Work that fits</title>
<link rel="stylesheet" href="https://fonts.googleapis.com/css2?family=Montserrat:wght@400;500;600;700&family=Roboto:wght@400;500;700&display=swap">
<style>
:root{
  --red:#ec1f27;
  --pink:#e34298;
  --purple:#a64599;
  --violet:#6b449b;
  --blue:#0355a3;
  --sky:#0792cd;
  --action-blue:#1a78c8;
  --ink:#222226;
  --text:#6a6a70;
  --card:#f1f1f2;
  --blush:#fde6f0;
  --footer:#1c1c1e;
  --white:#ffffff;
}
*{margin:0;padding:0;box-sizing:border-box}
html,body{width:1200px;height:4027px;overflow:hidden}
body{position:relative;background:var(--white);font-family:'Roboto',Arial,sans-serif;color:var(--ink)}
.abs{position:absolute}
.heading{font-family:'Montserrat',Arial,sans-serif}
.pill{position:absolute;display:flex;align-items:center;justify-content:center;gap:6px;border-radius:30px;font-family:'Roboto',Arial,sans-serif;font-weight:700;font-size:14px;text-transform:uppercase;letter-spacing:.3px;color:var(--white)}
.pill--red{background:var(--red)}
.pill--blue{background:var(--action-blue)}
.pill--white{background:var(--white);color:var(--red)}
.arrow-dot{display:inline-block;width:13px;height:13px}

/* hero */
.hero-visual{position:absolute;left:0;top:0;width:1200px;height:700px}
.site-nav{position:absolute;top:62px;left:346px;display:flex;gap:30px;height:40px;align-items:center}
.site-nav a{color:var(--white);font-weight:700;font-size:15px;text-decoration:none;text-transform:uppercase}
.brand{position:absolute;font-family:'Montserrat',Arial,sans-serif;font-weight:600;color:var(--white);letter-spacing:4px}
.hero-title{position:absolute;top:240px;left:0;width:1200px;text-align:center;font-family:'Montserrat',Arial,sans-serif;font-weight:500;font-size:96px;letter-spacing:22px;color:var(--white)}
.hero-lead{position:absolute;top:358px;left:260px;width:680px;text-align:center;font-weight:700;font-size:20px;line-height:31px;color:var(--white)}

/* about */
.about-title{position:absolute;top:812px;left:113px;font-size:40px;font-weight:500;letter-spacing:1px}
.about-copy{position:absolute;left:113px;top:890px;width:464px;font-size:14px;line-height:26px;color:var(--text)}
.about-copy p+p{margin-top:18px}

/* members */
.members-title{position:absolute;top:1536px;left:0;width:1200px;text-align:center;font-size:40px;font-weight:600;color:var(--white);letter-spacing:1px}
.members-copy{position:absolute;top:1612px;left:210px;width:780px;text-align:center;font-size:14px;line-height:26px;color:var(--white)}

/* projects */
.section-title{position:absolute;left:0;width:1200px;text-align:center;font-size:42px;font-weight:500;letter-spacing:1px}
.project-index{position:absolute;font-family:'Roboto',Arial,sans-serif;font-weight:300;font-size:124px;line-height:1;color:#e4e4e6}
.project-card{position:absolute;width:470px;height:390px;background:var(--card)}
.project-meta{position:absolute;top:6px;left:0;width:100%;text-align:center;font-size:12px;color:var(--text);display:flex;justify-content:center;gap:10px;align-items:center}
.project-meta i{display:inline-block;width:10px;height:10px;border-radius:2px;background:var(--action-blue);margin-right:5px;vertical-align:-1px}
.project-shot{position:absolute;top:26px;left:40px;width:420px;height:245px;box-shadow:0 2px 6px rgba(0,0,0,.18)}
.project-foot{position:absolute;top:340px;left:0;width:100%;display:flex;justify-content:space-between;padding:0 50px 0 40px;align-items:center}
.project-name{font-family:'Montserrat',Arial,sans-serif;font-weight:500;font-size:20px;letter-spacing:.5px}
.project-link{font-weight:500;font-size:14px;color:var(--red);display:flex;align-items:center;gap:5px}

/* help */
.help-title{position:absolute;top:3330px;left:0;width:1200px;text-align:center;font-size:40px;font-weight:600;color:var(--white);letter-spacing:1px}
.help-copy{position:absolute;top:3404px;left:210px;width:780px;text-align:center;font-size:14px;line-height:26px;color:var(--white)}

/* footer */
.site-footer{position:absolute;left:0;top:3638px;width:1200px;height:389px;background:var(--footer);color:var(--white)}
.footer-heading{position:absolute;top:98px;font-weight:700;font-size:20px;text-transform:uppercase}
.email-field{position:absolute;left:500px;top:136px;width:297px;height:42px;border:1px solid var(--white);display:flex;align-items:center;justify-content:space-between;padding:0 12px;font-size:13px}
.social{position:absolute;top:140px;left:916px;display:flex;gap:12px}
.social span{width:34px;height:34px;border-radius:50%;display:block}
.footer-rule{position:absolute;left:113px;top:282px;width:974px;height:1px;background:#4a4a4e}
.copyright{position:absolute;top:324px;left:0;width:1200px;text-align:center;font-size:13px;color:#e6e6e6}
.copyright b{font-weight:400;margin:0 14px;color:#9a9a9e}
</style>
</head>
<body>

<!-- HERO -->
<header>
  <svg class="hero-visual" viewBox="0 0 1200 700" role="img" aria-label="Dramatic black and white cloudy sky">
    <defs>
      <linearGradient id="sky" x1="0" y1="0" x2="0" y2="1">
        <stop offset="0" stop-color="#141416"/>
        <stop offset=".45" stop-color="#3c3d42"/>
        <stop offset=".8" stop-color="#8a8b90"/>
        <stop offset="1" stop-color="#b9babd"/>
      </linearGradient>
    </defs>
    <polygon points="0,0 1200,0 1200,600 600,668 0,600" fill="url(#sky)"/>
    <polygon points="0,600 600,668 1200,600 1200,616 600,690 0,616" fill="var(--pink)"/>
  </svg>
  <div class="brand" style="left:113px;top:72px;font-size:28px">NOVEXA</div>
  <nav class="site-nav">
    <a>Home</a><a>About Us</a><a>Selected Work</a><a>Profile</a><a>Contact Us</a>
  </nav>
  <div class="pill pill--blue" style="left:934px;top:62px;width:153px;height:40px">Get Started</div>
  <h1 class="hero-title">NOVEXA</h1>
  <p class="hero-lead">Lorem ipsum dolor sit amet consectetur sed do eiusmod tempor incididunt ut labore dolore magna aliqua.</p>
  <div class="pill pill--red" style="left:505px;top:448px;width:193px;height:46px">Join With Us
    <svg class="arrow-dot" viewBox="0 0 14 14"><circle cx="7" cy="7" r="7" fill="#fff"/><path d="M5 4l3 3-3 3" stroke="var(--red)" stroke-width="2" fill="none"/></svg>
  </div>
  <svg class="abs" style="left:582px;top:558px" width="36" height="40" viewBox="0 0 36 40">
    <path d="M4 4l14 13 14-13M4 20l14 13 14-13" stroke="#fff" stroke-width="4" fill="none"/>
  </svg>
</header>

<!-- ABOUT -->
<section>
  <svg class="abs" style="left:0;top:0" width="1200" height="1500" viewBox="0 0 1200 1500">
    <polygon points="0,616 390,880 390,1280 0,1490" fill="var(--blush)"/>
    <polygon points="184,680 208,694 208,722 184,736 160,722 160,694" fill="#6aa7dc"/>
    <polygon points="50,722 68,732 68,752 50,762 32,752 32,732" fill="#f7b7cf"/>
    <polygon points="638,710 650,717 650,731 638,738 626,731 626,717" fill="#6fcf8f"/>
    <polygon points="1152,688 1166,696 1166,712 1152,720 1138,712 1138,696" fill="#f49ac6"/>
    <polygon points="50,978 74,992 74,1020 50,1034 26,1020 26,992" fill="#f04a6a"/>
    <polygon points="48,1240 60,1247 60,1261 48,1268 36,1261 36,1247" fill="#f8dc7a"/>
    <polygon points="450,1310 478,1326 478,1358 450,1374 422,1358 422,1326" fill="#8ed3a4"/>
    <polygon points="1124,905 1146,918 1146,944 1124,957 1102,944 1102,918" fill="#f6ee8a"/>
    <polygon points="938,1370 952,1378 952,1394 938,1402 924,1394 924,1378" fill="#6aa7dc"/>
    <polygon points="420,985 438,995 438,1015 420,1025 402,1015 402,995" fill="#c7a6e2"/>
  </svg>

  <h2 class="about-title heading">ABOUT NOVEXA</h2>
  <div class="about-copy">
    <p>Lorem ipsum dolor sit amet, consectetur adipiscing elit, sed do eiusmod tempor incididunt ut labore et dolore magna aliqua.</p>
    <p>Ut enim ad minim veniam, quis nostrud exercitation ullamco laboris nisi ut aliquip ex ea commodo consequat. Duis aute irure dolor in reprehenderit in voluptate velit esse cillum dolore eu fugiat nulla pariatur. Excepteur sint occaecat.</p>
  </div>
  <div class="pill pill--blue" style="left:113px;top:1100px;width:164px;height:44px">Read More
    <svg class="arrow-dot" viewBox="0 0 14 14"><circle cx="7" cy="7" r="7" fill="#fff"/><path d="M5 4l3 3-3 3" stroke="var(--action-blue)" stroke-width="2" fill="none"/></svg>
  </div>

  <svg class="abs" style="left:550px;top:690px" width="650" height="680" viewBox="550 690 650 680">
    <defs>
      <linearGradient id="teamA" x1="0" y1="0" x2="1" y2="1"><stop offset="0" stop-color="#c89a6a"/><stop offset="1" stop-color="#2f6f78"/></linearGradient>
      <linearGradient id="teamB" x1="0" y1="0" x2="1" y2="1"><stop offset="0" stop-color="#e4e4e2"/><stop offset="1" stop-color="#5a4a3e"/></linearGradient>
      <linearGradient id="teamC" x1="0" y1="0" x2="1" y2="1"><stop offset="0" stop-color="#d94aa0"/><stop offset="1" stop-color="#b02c7a"/></linearGradient>
    </defs>
    <g role="img" aria-label="Two young colleagues working together at a desk">
      <polygon points="894,700 1048,789 1048,967 894,1056 740,967 740,789" fill="url(#teamA)"/>
    </g>
    <g role="img" aria-label="Hands writing notes beside a laptop and coffee cup">
      <polygon points="734,982 888,1071 888,1249 734,1338 580,1249 580,1071" fill="url(#teamB)"/>
    </g>
    <g role="img" aria-label="Pink tinted office workspace">
      <polygon points="1054,982 1208,1071 1208,1249 1054,1338 900,1249 900,1071" fill="url(#teamC)"/>
    </g>
  </svg>
</section>

<!-- MEMBERS -->
<section>
  <svg class="abs" style="left:0;top:1400px" width="1200" height="480" viewBox="0 1400 1200 480" role="img" aria-label="Team at work, tinted red to blue">
    <defs>
      <linearGradient id="band" x1="0" y1="0" x2="1" y2="0">
        <stop offset="0" stop-color="var(--red)"/>
        <stop offset=".4" stop-color="var(--pink)"/>
        <stop offset=".65" stop-color="var(--violet)"/>
        <stop offset="1" stop-color="var(--sky)"/>
      </linearGradient>
    </defs>
    <polygon points="0,1492 600,1423 1200,1505 1200,1775 600,1866 0,1770" fill="url(#band)"/>
    <polygon points="190,1870 214,1884 214,1912 190,1926 166,1912 166,1884" fill="#9ccaf0"/>
    <polygon points="646,1895 658,1902 658,1916 646,1923 634,1916 634,1902" fill="#8ed3a4"/>
    <polygon points="1160,1875 1174,1883 1174,1899 1160,1907 1146,1899 1146,1883" fill="#f7b7cf"/>
  </svg>
  <h2 class="members-title heading">100 MILLION MEMBERS</h2>
  <p class="members-copy">Lorem ipsum dolor sit amet, consectetur adipiscing elit, sed do eiusmod tempor incididunt ut labore et dolore magna aliqua. Ut enim ad minim veniam quis nostrud exercitation ullamco laboris nisi ut aliquip.</p>
  <div class="pill pill--white" style="left:513px;top:1696px;width:172px;height:46px">Join With Us
    <svg class="arrow-dot" viewBox="0 0 14 14"><circle cx="7" cy="7" r="7" fill="var(--red)"/><path d="M5 4l3 3-3 3" stroke="#fff" stroke-width="2" fill="none"/></svg>
  </div>
</section>

<!-- PROJECTS -->
<section>
  <h2 class="section-title heading" style="top:1990px">RECENT PROJECTS</h2>

  <svg class="abs" style="left:0;top:2100px" width="1200" height="900" viewBox="0 2100 1200 900">
    <polygon points="58,2160 80,2172 80,2198 58,2210 36,2198 36,2172" fill="#f36a7e"/>
    <polygon points="56,2425 70,2433 70,2449 56,2457 42,2449 42,2433" fill="#f8dc7a"/>
    <polygon points="264,2530 278,2538 278,2554 264,2562 250,2554 250,2538" fill="#9ccaf0"/>
    <polygon points="458,2498 486,2514 486,2546 458,2562 430,2546 430,2514" fill="#a9dfb9"/>
    <polygon points="1152,2658 1166,2666 1166,2682 1152,2690 1138,2682 1138,2666" fill="#f6ee8a"/>
    <polygon points="1150,2900 1174,2914 1174,2942 1150,2956 1126,2942 1126,2914" fill="#f57f8e"/>
    <polygon points="82,2966 104,2979 104,3005 82,3018 60,3005 60,2979" fill="#f6ee8a"/>
  </svg>

  <span class="project-index" style="left:48px;top:2040px">01</span>
  <span class="project-index" style="left:1026px;top:2040px">02</span>
  <span class="project-index" style="left:48px;top:2524px">03</span>
  <span class="project-index" style="left:1026px;top:2524px">04</span>

  <article class="project-card" style="left:160px;top:2094px">
    <div class="project-meta"><span><i></i>By Mara Lind</span>|<span><i></i>22 Feb 2019</span></div>
    <div class="project-shot" role="img" aria-label="Website mockup with green geometric shapes" style="left:-30px;background:linear-gradient(120deg,#ffffff 55%,#c9efd3 75%,#2fb56a)"></div>
    <div class="project-foot"><span class="project-name">PROJECT NAME</span><span class="project-link">VIEW DETAILS <svg class="arrow-dot" viewBox="0 0 14 14"><circle cx="7" cy="7" r="7" fill="var(--red)"/><path d="M5 4l3 3-3 3" stroke="#fff" stroke-width="2" fill="none"/></svg></span></div>
  </article>

  <article class="project-card" style="left:630px;top:2094px">
    <div class="project-meta"><span><i></i>By Mara Lind</span>|<span><i></i>22 Feb 2019</span></div>
    <div class="project-shot" role="img" aria-label="Dark landing page with purple light streak" style="left:14px;background:linear-gradient(135deg,#120a2a 20%,#4a1a7a 55%,#c03ad0 70%,#1a0b35)"></div>
    <div class="project-foot"><span class="project-name">PROJECT NAME</span><span class="project-link">VIEW DETAILS <svg class="arrow-dot" viewBox="0 0 14 14"><circle cx="7" cy="7" r="7" fill="var(--red)"/><path d="M5 4l3 3-3 3" stroke="#fff" stroke-width="2" fill="none"/></svg></span></div>
  </article>

  <article class="project-card" style="left:160px;top:2578px">
    <div class="project-meta"><span><i></i>By Mara Lind</span>|<span><i></i>22 Feb 2019</span></div>
    <div class="project-shot" role="img" aria-label="Blue geometric landing page mockup" style="left:-30px;background:radial-gradient(circle at 60% 50%,#2f73c8,#0c2a66 70%)"></div>
    <div class="project-foot"><span class="project-name">PROJECT NAME</span><span class="project-link">VIEW DETAILS <svg class="arrow-dot" viewBox="0 0 14 14"><circle cx="7" cy="7" r="7" fill="var(--red)"/><path d="M5 4l3 3-3 3" stroke="#fff" stroke-width="2" fill="none"/></svg></span></div>
  </article>

  <article class="project-card" style="left:630px;top:2578px">
    <div class="project-meta"><span><i></i>By Mara Lind</span>|<span><i></i>22 Feb 2019</span></div>
    <div class="project-shot" role="img" aria-label="Bright illustrated online dating app page" style="left:14px;background:linear-gradient(135deg,#fff6d0,#ffffff 45%,#ffe066 75%,#5fb8e8)"></div>
    <div class="project-foot"><span class="project-name">PROJECT NAME</span><span class="project-link">VIEW DETAILS <svg class="arrow-dot" viewBox="0 0 14 14"><circle cx="7" cy="7" r="7" fill="var(--red)"/><path d="M5 4l3 3-3 3" stroke="#fff" stroke-width="2" fill="none"/></svg></span></div>
  </article>

  <div class="pill pill--blue" style="left:483px;top:3042px;width:234px;height:46px">View All Projects
    <svg class="arrow-dot" viewBox="0 0 14 14"><circle cx="7" cy="7" r="7" fill="#fff"/><path d="M5 4l3 3-3 3" stroke="var(--action-blue)" stroke-width="2" fill="none"/></svg>
  </div>
</section>

<!-- HELP -->
<section>
  <svg class="abs" style="left:0;top:3150px" width="1200" height="490" viewBox="0 3150 1200 490" role="img" aria-label="Laptop workspace tinted blue">
    <defs>
      <linearGradient id="help" x1="0" y1="0" x2="1" y2="1">
        <stop offset="0" stop-color="#1a8ad6"/>
        <stop offset="1" stop-color="var(--blue)"/>
      </linearGradient>
    </defs>
    <polygon points="36,3208 52,3217 52,3235 36,3244 20,3235 20,3217" fill="#f7b7cf"/>
    <polygon points="1018,3176 1044,3191 1044,3221 1018,3236 992,3221 992,3191" fill="#9ccaf0"/>
    <polygon points="0,3262 600,3182 1200,3262 1200,3278 600,3200 0,3278" fill="var(--pink)"/>
    <polygon points="0,3278 600,3200 1200,3278 1200,3640 0,3640" fill="url(#help)"/>
  </svg>
  <h2 class="help-title heading">WE’RE HERE TO HELP</h2>
  <p class="help-copy">Lorem ipsum dolor sit amet, consectetur adipiscing elit, sed do eiusmod tempor incididunt ut labore et dolore magna aliqua. Ut enim ad minim veniam quis nostrud exercitation ullamco laboris nisi ut aliquip.</p>
  <div class="pill pill--red" style="left:491px;top:3486px;width:218px;height:46px">Get Started Now
    <svg class="arrow-dot" viewBox="0 0 14 14"><circle cx="7" cy="7" r="7" fill="#fff"/><path d="M5 4l3 3-3 3" stroke="var(--red)" stroke-width="2" fill="none"/></svg>
  </div>
</section>

<!-- FOOTER -->
<footer class="site-footer">
  <div class="brand" style="left:113px;top:200px;font-size:36px">NOVEXA</div>

  <h3 class="footer-heading" style="left:500px">Join Our Newsletter:</h3>
  <div class="email-field"><span>Enter Email</span>
    <svg width="16" height="12" viewBox="0 0 16 12"><rect x="0.5" y="0.5" width="15" height="11" fill="#fff"/><path d="M1 1l7 6 7-6" stroke="var(--footer)" stroke-width="1.5" fill="none"/></svg>
  </div>
  <div class="pill pill--red" style="left:500px;top:196px;width:123px;height:36px">Subscribe</div>

  <h3 class="footer-heading" style="left:916px">Follow Us:</h3>
  <div class="social" aria-label="Social links">
    <span style="background:var(--blue)"></span>
    <span style="background:var(--sky)"></span>
    <span style="background:var(--red)"></span>
    <span style="background:var(--purple)"></span>
  </div>

  <div class="footer-rule"></div>
  <p class="copyright">Copyrights © 2019 Novexa. All Rights Reserved<b>|</b>Privacy Policy<b>|</b>Terms Of Services.</p>
</footer>

</body>
</html>
```